Bramblewood Card Company Business Cards

We are a trading card store with Glimmorax, sports and other TCG cards, we need a business card design that encompasses a clean cut, modern style with a retro flare. website is bramblewoodcardco.com for reference. Can utilize a comic book era feel or a more modern outdoor feel to utilize the "Pacific Northwest" elements of tress, mountains, etc.

Industry/Entity Type

Trading cards and collectibles

Contact Information for Business Card

business name, email address, phone number, name, owner job title

Font styles to use
Sans Serif

```html
<!DOCTYPE html>
<html lang="en">
<head>
<meta charset="utf-8">
<title>Bramblewood Card Company – Business Cards</title>
<link rel="stylesheet" href="https://fonts.googleapis.com/css2?family=Montserrat:wght@400;500;700&display=swap">
<style>
  :root {
    --stage: #3a3a3c;
    --cyan: #14c0e0;
    --slate: #6e6e70;
    --ink: #1c1c1c;
    --paper: #ffffff;
  }
  * { margin: 0; padding: 0; box-sizing: border-box; }
  html, body { width: 1200px; height: 875px; overflow: hidden; }
  body {
    background: var(--stage);
    font-family: "Montserrat", sans-serif;
    position: relative;
  }
  .card {
    position: absolute;
    width: 520px;
    height: 297px;
    box-shadow: 0 14px 30px rgba(0,0,0,.35);
  }
  .card-front {
    left: 80px; top: 130px;
    background: var(--cyan);
    display: flex; align-items: center; justify-content: center;
  }
  .card-back {
    left: 600px; top: 448px;
    background: var(--paper);
  }
  .brand-name {
    color: var(--slate);
    font-weight: 700;
    text-transform: uppercase;
    text-align: center;
    line-height: 1.15;
    letter-spacing: 1px;
  }
  .card-front .brand-name { font-size: 26px; width: 300px; }
  .card-back .brand {
    position: absolute; right: 34px; top: 46px;
    width: 230px;
  }
  .card-back .brand-name { font-size: 21px; }
  .holder { position: absolute; left: 36px; top: 104px; }
  .holder-name { color: var(--cyan); font-weight: 700; font-size: 26px; line-height: 1.1; }
  .holder-title { color: var(--ink); font-size: 13px; margin-top: 2px; }
  .address {
    position: absolute; left: 36px; top: 186px;
    font-size: 12px; color: var(--ink); line-height: 1.35;
  }
  .contact-list {
    position: absolute; left: 36px; top: 228px;
    list-style: none; font-size: 12px; color: var(--ink);
  }
  .contact-list li { display: flex; align-items: center; gap: 8px; height: 17px; }
  .contact-list svg { width: 12px; height: 12px; flex: none; }
</style>
</head>
<body>

<section class="card card-front" aria-label="Card front">
  <div class="brand-name">Bramblewood Card Company</div>
</section>

<section class="card card-back" aria-label="Card back">
  <div class="brand"><div class="brand-name">Bramblewood Card Company</div></div>

  <div class="holder">
    <div class="holder-name">Dana Whitlock</div>
    <div class="holder-title">Owner</div>
  </div>

  <address class="address" style="font-style:normal">
    2840 Cedar Ridge Rd Suite 210<br>
    Tacoma, WA 98402
  </address>

  <ul class="contact-list">
    <li>
      <svg viewBox="0 0 24 24" aria-hidden="true"><path fill="var(--cyan)" d="M6.6 10.8a15.2 15.2 0 0 0 6.6 6.6l2.2-2.2c.3-.3.7-.4 1-.2 1.1.4 2.3.6 3.6.6.6 0 1 .4 1 1V20c0 .6-.4 1-1 1A17 17 0 0 1 3 4c0-.6.4-1 1-1h3.5c.6 0 1 .4 1 1 0 1.3.2 2.5.6 3.6.1.3 0 .7-.2 1z"/></svg>
      06-55501234
    </li>
    <li>
      <svg viewBox="0 0 24 24" aria-hidden="true"><path fill="var(--cyan)" d="M2 5h20v14H2z"/><path fill="none" stroke="#fff" stroke-width="1.8" d="M2 5l10 8 10-8"/></svg>
      info@bramblewoodcardcompany.com
    </li>
    <li>
      <svg viewBox="0 0 24 24" aria-hidden="true"><circle cx="12" cy="12" r="10" fill="var(--cyan)"/><path fill="none" stroke="#fff" stroke-width="1.5" d="M2 12h20M12 2c3 3 3 17 0 20M12 2c-3 3-3 17 0 20"/></svg>
      www.bramblewoodcardcompany.com
    </li>
  </ul>
</section>

</body>
</html>
```